Talvoro Web Design

We need a redesign of our current website www.talvoro-example.com

THIS IS A DESIGN STAGE ONLY

We have attached details of the whole project for your understanding only

We do not want to change our Logo but do want to have a more modern and intuitive feel to the site.

The first stage is the design but we are also looking for a coder to take the site to the next level

Talvoro has a current website that has been in operation for the past 6 years the design was based around the Saas self-service model and while functional does not meet Talvoro needs with regard to the new positioning.

We are happy to stay in Joomla or will look at alternatives

The purpose of the redesign is to align the look and feel of the website to meet our current new brand position and to provide a access point for the delivery of new content from Blogs and white papers as well as a portal for information for our current users for gathering Tips and Tricks and access to additional resources to assist them to provide feedback and get support.

Talvoro is Australia's only PPM (Project and Portfolio Management) software provider that caters to the needs of project managers and C-level executives looking for insights into the alignment of resources to business strategy and investment decisions.

As companies gain maturity in PPM there is a need for innovation and management of change beyond just implementation of tools this is why Talvoro has evolved from being a SaaS to becoming a SwS (Software with Service) provider.

Talvoro is recognized as the tool of choice amongst program and project managers that is able to provide the user with an intuitive reliable interface that is capable of evolving and maturing to meet and exceed client requirements.

We are able to provide people at the coalface with tools that enable them to manage resources, scope, time sheeting, issues, changes and risk with excellent reporting functionality.

For C-level executives we are able to provide Business Intelligence (BI) functionality and reporting by integrating the PPM data with other business management systems such as ERP and CRM to provide a insight beyond pure PPM reporting.

We are able to provide Project Management insights from years of experience working with our clients in developing solutions that are inline with the evolution that comes with change.

Please feel free to email me on marcus.hale@talvoro-example.com if you require any further details. A Site map and a wire frame is available.

Competitor sites include

www.plenvix-example.com
www.corbelo-example.com
www.quandrit-example.com
www.vestrel-example.com
Updates

Hi All 

We are getting some great designs coming in and really appreciate all of your efforts.

Some feedback to you all is that we have a preference for cleaner designs that take into account comprehension ability. So reverse type to us looks good but doesnt always get the cut through.

We have to remember that this is a marketing site first and foremost so what we are looking for is the ability to engage with our audience and get them to start to explore. That is upto us to provide great content and what we want from the design is the ability to be be able to engage with our Audience.

For your consideration please review this info from our marketing plan

There are 3 main communication groups inthe sales process.

Users-        These are the peoplewho will be at the coal face inputting the data and using the product on adaily basis. It is key to provide them with an easy to use and functional toolthat is able to provide them with the information they are looking for easily andintuitively. They have the capacity to say yes and can push the sale decisionup the chain. They equally have the power to say No and stop the sales processin its tracks. They will have a opinion who or what they feel is the best ofbreed and will try to influence the process.

Users are split into two groups.

Group1- They will be diploma if not degree qualifiedwill be a mix of Male and female with majority aged 18 to 35 they are at thecareer development stage of their life cycle normally on an income 45k to 70kper annum. We would position these people very strongly in the “What is in itfor me”.

Group2- PM who has used a variety of tools and systemsover the years they will be pre disposed to one or more systems and has morethan likely been exposed to MSP. Usually in the 30 to 50 year old age rangewith extensive on the job experience.

KeyInfluencers- These are the people who while notactually utilizing the software need to receive information in the form ofreports etc from the system. They normally don’t have the capacity to say yesbut they most certainly can say no. They will have come from a PM or IT roleand have a strong understanding of the PM processes. Influencers will be 30 to50 years of age they are at the family development stage with strong demandsfrom work and family predominantly male but not exclusively. They would bedegree qualified and possibly have completed or looking at additional studies. Therewill be an emphasis on getting the job done right. They are very time poor and hardto communicate with and engage. While being time poor they have an affinitywith and understand the greater good.

DecisionMakers- These are our key decision makers whilethey may not have direct input into the system or processes they are at the endof the day the people who approve the expenditure.

There is a huge demand for this person’stime with a multitude of people from internal employees and management,suppliers, customers, the community and potential suppliers. They are oftentravelling and going from one subject matter to another meeting after meeting.They will be at the stage where children are gaining some independents or leftthe home, career is stabilized and a clear path is formed. They are very directand deal in the facts and figures when it comes to decision making, they arenormally highly educated to the MBA or Doctorate level. They will be driven byoutcomes not the process of getting there.

 

A consistent theme across this group isthe following.

Psychographics

·Values time and considers ittheir single most limited resource.

·Excited about accepting andusing innovative ideas and products always wants to be at the fore front.

·Value adding has priority overprice

·Consistent web users: preferinternet over magazines and newspapers

Behavior

·They are leaders in productselection and respond to the opinions of the ‘Industry Experts’ when makingpurchase decisions.

·This group will look to theinternet to acquire the information

·Will make an informed decisionto purchase after due consideration.

·This group can be a powerfulsales force resulting from the referral network they build and use

Hope this helps

Hi All

Sorry for the delay we are in the final stages of decisions, so sorry we have had people away from the office who need to be involved in the process.

We will submit individual questions to those in the running and let all of the people who didnt get through this time as to why shortly.

We would like to thank you all for your efforts and submissions.

Regards

Marcus Hale 

Industry/Entity Type

Business Management

Requirements
Must have
• The scope of the website is to provide a modern functional website that is easy to navigate and provides a range of products and services to meet the needs of our potential clients and current users.

Two potential groups of viewers exist:
1. Potential Clients and users from the Project management community these would be split into 3 distinct groups. ( Please refer to Page 20 Talvoro marketing Plan)
a. Project Managers
b. Project Directors
c. Business Managers
2. Current Talvoro Users

The goal of website is to engage with the project management community reinforcing the Talvoro Brand as Software with Service the key ethos should be around the company being thought leaders and industry experts with a strong commitment to clients and the success of their Portfolio/Program Management Office

Maintaining a modern and user friendly site is of the highest importance in order to hold users attention and guide the viewer to information that will lead to a decision to pursue accreditation and association with the Talvoro Brand

We would like to guide potential clients to want to engage with us in assisting them to understand their current position in the P3M3 maturity model and to use us as a source for information and guidance.

Benefits for using the site should include:
• Information from a broad spectrum of Project Management professionals and recognized industry experts.
• Information on the Talvoro Product and Services
• Timely and up to date information that encourages readers to return to the site
• Call to action, and plans for potential users of Talvoro software.
• Demonstrate the benefits of accreditation and Call to action for current users to gain accreditation.
• Call to action for attending monthly webinars
• Ability to review past webinars, whitepapers etc.

```html
<!DOCTYPE html>
<html lang="en">
<head>
<meta charset="utf-8">
<title>Talvoro – Project Management Software</title>
<link href="https://fonts.googleapis.com/css2?family=PT+Sans+Narrow:wght@700&family=Source+Sans+3:ital,wght@0,300;0,400;0,600;0,700;1,600&display=swap" rel="stylesheet">
<style>
:root{
  --orange:#f26a2a;
  --orange-light:#f7923a;
  --red:#e6401c;
  --red-dark:#8a2410;
  --black:#111;
  --ink:#3a3a3a;
  --text:#4a4a4a;
  --grey:#efefef;
  --line:#e2e2e2;
  --white:#fff;
  --footer-text:#dcdcdc;
  --muted:#9a9a9a;
}
*{margin:0;padding:0;box-sizing:border-box}
html,body{width:1200px;height:1200px;overflow:hidden;background:var(--white)}
body{position:relative;font-family:"Source Sans 3",sans-serif;color:var(--text)}
.abs{position:absolute}

/* top navigation */
.main-nav{left:100px;top:14px;width:1001px;height:52px;border-radius:4px;
  background:linear-gradient(#f57a3a,#ef4b22);box-shadow:0 1px 2px rgba(0,0,0,.25)}
.main-nav a{position:absolute;top:0;height:52px;line-height:52px;color:var(--white);
  font-family:"PT Sans Narrow",sans-serif;font-weight:700;font-size:18.5px;text-decoration:none;
  text-shadow:0 1px 1px rgba(0,0,0,.25)}
.main-nav a.active{background:var(--red);padding:0 20px 0 25px}

/* header */
.header{left:99px;top:71px;width:1002px;height:97px;border-radius:3px;
  background:linear-gradient(#2b2b2b,#050505)}
.brand-name{left:37px;top:24px;font-size:42px;font-weight:400;color:var(--white);line-height:1}
.brand-tagline{left:196px;top:22px;font-size:13px;font-weight:600;color:var(--white);white-space:nowrap}
.sub-nav a{position:absolute;top:34px;font-size:17px;color:var(--white);text-decoration:none}
.sub-nav a.current{color:var(--orange-light)}

/* hero */
.hero{left:101px;top:172px;width:999px;height:356px;
  background:radial-gradient(ellipse 420px 300px at 300px 330px,#fbb22c 0%,#f78a2a 45%,transparent 80%),
             linear-gradient(90deg,#ef4824,#f46a2a 45%,#f06a2c 70%,#ef5a28);
  box-shadow:6px 4px 14px rgba(0,0,0,.12)}
.hero-art{left:40px;top:58px;width:450px;height:262px;border-radius:8px;
  background:linear-gradient(90deg,rgba(90,90,90,.35),rgba(20,20,20,.55) 50%,rgba(240,120,40,.35))}
.hero h1{left:515px;top:121px;font-size:43.5px;font-weight:600;color:var(--white);letter-spacing:.5px;line-height:1;white-space:nowrap}
.hero p{left:516px;top:172px;font-size:20px;font-weight:600;color:var(--white);white-space:nowrap}
.read-more{left:821px;top:218px;width:97px;height:35px;border-radius:4px;
  background:linear-gradient(#fff,#dcdcdc);color:#333;font-size:15px;text-align:center;line-height:35px;
  box-shadow:0 4px 8px rgba(0,0,0,.2)}
.slider-arrow{top:288px;width:30px;height:30px;border-radius:50%;background:var(--red-dark);box-shadow:0 1px 2px rgba(0,0,0,.3)}
.slider-arrow svg{display:block}

/* side tabs */
.side-tab{background:linear-gradient(90deg,#333,#0a0a0a);border-radius:4px 0 0 4px}
.side-tab span{position:absolute;left:50%;top:50%;transform:translate(-50%,-50%) rotate(-90deg);white-space:nowrap;font-size:16px}
.tab-newsletter{left:70px;top:193px;width:31px;height:162px}
.tab-newsletter span{color:#e8e8e8}
.tab-trial{left:59px;top:365px;width:42px;height:163px}
.tab-trial span{color:var(--red);font-size:17px}

/* products */
.section-title{left:0;top:546px;width:1200px;text-align:center;font-size:20.8px;font-weight:700;color:var(--ink);letter-spacing:.2px}
.product{top:585px;width:231px;height:328px;border:1px solid var(--line);background:var(--white);
  box-shadow:inset 0 0 0 5px #f7f7f7}
.product h2{position:absolute;left:0;top:24px;width:100%;text-align:center;font-size:19.5px;font-weight:400;color:var(--red)}
.product .photo{position:absolute;left:10px;top:54px;width:211px;height:106px}
.product p{position:absolute;left:19px;top:166px;width:192px;text-align:center;font-size:14px;line-height:20px;color:var(--text)}
.product .download{position:absolute;left:24px;top:277px;width:183px;height:35px;border-radius:2px;
  background:linear-gradient(#2c2c2c,#000);color:var(--white);font-size:17px;font-weight:300;text-align:center;line-height:35px}

.section-shadow{left:100px;top:930px;width:1000px;height:22px;
  background:radial-gradient(ellipse 500px 10px at 50% 100%,rgba(0,0,0,.18),transparent)}

/* partner strip */
.partners{left:99px;top:953px;width:1002px;height:91px;background:linear-gradient(#f7f7f7,#ececec);border-radius:3px}
.partner{position:absolute;top:36px;font-size:21px;font-weight:700;color:#7d7d7d;white-space:nowrap}
.partner i{display:inline-block;width:14px;height:14px;border-radius:50%;background:#9a9a9a;margin-right:6px;vertical-align:1px}
.partner.accent i{background:var(--red)}

/* footer */
.footer{left:1px;top:1057px;width:1199px;height:143px;
  background:radial-gradient(ellipse 600px 160px at 50% 0%,#2a2a2a,#050505)}
.footer ul{position:absolute;top:19px;list-style:none}
.footer li{font-size:13px;line-height:24px;color:var(--footer-text)}
.social{top:25px;width:32px;height:32px;border-radius:50%;background:linear-gradient(#fafafa,#bcbcbc)}
.copyright{left:761px;top:78px;font-size:13px;color:var(--muted);white-space:nowrap}
</style>
</head>
<body>

<nav class="abs main-nav">
  <a class="active" style="left:41px">HOME</a>
  <a style="left:147px">FAQ</a>
  <a style="left:215px">DOWNLOAD</a>
  <a style="left:339px">SUPPORT &amp; TRAINING</a>
  <a style="left:528px">CUSTOMERS</a>
  <a style="left:652px">ABOUT US</a>
  <a style="left:762px">LOGIN</a>
  <a style="left:845px">CONTACT US</a>
</nav>

<header class="abs header">
  <span class="abs brand-name">Talvoro</span>
  <span class="abs brand-tagline">from to-do to done</span>
  <nav class="sub-nav">
    <a class="current" style="left:640px">Tour</a>
    <a style="left:717px">Features</a>
    <a style="left:825px">Pricing</a>
    <a style="left:918px">Sign up</a>
  </nav>
</header>

<section class="abs hero">
  <div class="abs hero-art" role="img" aria-label="Puzzle pieces with chart icons flanking a group of business people in silhouette"></div>
  <h1 class="abs">PROJECT MANGEMENT</h1>
  <p class="abs">Simple, easy to use project management software.</p>
  <div class="abs read-more">Read more</div>
  <div class="abs slider-arrow" style="left:832px">
    <svg width="30" height="30" viewBox="0 0 30 30"><path d="M17 10 L12 15 L17 20 Z" fill="#fff"/></svg>
  </div>
  <div class="abs slider-arrow" style="left:873px">
    <svg width="30" height="30" viewBox="0 0 30 30"><path d="M13 10 L18 15 L13 20 Z" fill="#fff"/></svg>
  </div>
</section>

<div class="abs side-tab tab-newsletter"><span>Subscribe Newsletter</span></div>
<div class="abs side-tab tab-trial"><span>To Get a Free Trial</span></div>

<h2 class="abs section-title">PROJECT MANAGEMENT SOFTWARE</h2>

<article class="abs product" style="left:111px">
  <h2>Project Management</h2>
  <div class="photo" role="img" aria-label="Team of colleagues planning around a glass board" style="background:linear-gradient(90deg,#dfe6ee,#c9d3de 50%,#b9a594)"></div>
  <p>Simple, easy to use project man-agement software. Plan, Track and Improve your projects. Reduce costs and increase effi-ciency.</p>
  <div class="download">DOWNLOAD NOW</div>
</article>

<article class="abs product" style="left:360px">
  <h2>Timesheets</h2>
  <div class="photo" role="img" aria-label="Timesheet software shown on laptop, tablet and phone" style="background:radial-gradient(ellipse at 50% 55%,#3b5a86,#9fb4cf 45%,#fff 72%)"></div>
  <p>Powerful hosted project time and status collection. Track expenses and time. Have an audit trail on your time billing. Timesheet software</p>
  <div class="download">DOWNLOAD NOW</div>
</article>

<article class="abs product" style="left:609px">
  <h2>Resource Management</h2>
  <div class="photo" role="img" aria-label="Business team stacking hands together" style="background:linear-gradient(90deg,#3a3a3a,#c9957a 45%,#8a6a5a 70%,#2e2e2e)"></div>
  <p>Plan, manage and control work for your whole organisation or a single project. Resource man-</p>
  <div class="download">DOWNLOAD NOW</div>
</article>

<article class="abs product" style="left:858px">
  <h2>Issues, Risks and change</h2>
  <div class="photo" role="img" aria-label="Stack of grey stones with one red stone" style="background:radial-gradient(ellipse at 55% 55%,#6a6a6a,#a9a9a9 40%,#fff 75%)"></div>
  <p>Track and report on issues, risk and change. One click reports.</p>
  <div class="download">DOWNLOAD NOW</div>
</article>

<div class="abs section-shadow"></div>

<section class="abs partners" aria-label="Partners">
  <span class="partner" style="left:72px"><i></i>Parcella</span>
  <span class="partner" style="left:199px"><i></i>Dealvine</span>
  <span class="partner" style="left:342px">Brightmark</span>
  <span class="partner" style="left:501px">Plumtide</span>
  <span class="partner accent" style="left:619px"><i></i>Emberlo</span>
  <span class="partner" style="left:754px"><i></i>Sparesto</span>
</section>

<footer class="abs footer">
  <ul style="left:119px"><li>Home</li><li>FAQ</li><li>Support &amp; Training</li><li>Contact Us</li></ul>
  <ul style="left:276px"><li>Tour</li><li>Features</li><li>Pricing</li><li>Sign up</li></ul>
  <ul style="left:380px"><li>Careers</li><li>Privacy Policy</li><li>Terms of Sale</li><li>Sitemap</li></ul>
  <span class="abs social" style="left:954px" aria-label="Social profile"></span>
  <span class="abs social" style="left:989px" aria-label="Social profile"></span>
  <span class="abs social" style="left:1025px" aria-label="Social profile"></span>
  <p class="abs copyright">Copyright &nbsp;© 2003 &nbsp;talvoro pty. ltd. All Rights Reserved</p>
</footer>

</body>
</html>
```